Pawn & Gun store business card design

Hello! We would like a new business card design for our pawn & gun store. We loan money on items of value and sell firearms, jewelry, electronics & more.

Card will need to have the following information:

Business name - Prairie Nickel Pawn & Gun
Address - 2417 Hwy 53 S. Suite C Cedar Hollow, TX 75246
Employees name - Darren Kellum
Phone number - 972-613-8840
Email - PrairieNickelPawn@Mailvera.com
Website - PrairieNickelPawn.com

Somewhere on the card we would like it to say "Offering 10 Month Layaway!" & "We buy & loan on anything of value!". Our main store color is orange (please see logo). Logo does not have to be on the business card but it can be. Would like the back to have an area to write a note on the back. We like vintage things like old coins, collectables, firearms and more so think about this in the design. We want a business card as unique as our store!

Colors

Designer to choose colors to be used in the design.

Requirements
Nice to have
• Vintage Style

```html
<!DOCTYPE html>
<html lang="en">
<head>
<meta charset="utf-8">
<title>Prairie Nickel Pawn &amp; Gun — Business Card</title>
<link rel="stylesheet" href="https://fonts.googleapis.com/css2?family=Libre+Baskerville:wght@400;700&family=Lato:wght@400;700&display=swap">
<style>
  :root {
    --bg: #1c1c1c;
    --card: #ffffff;
    --orange: #d95f1e;
    --brown: #3b1e10;
    --ink: #2b2b2b;
    --faint: #e6e6e6;
    --rule: #d4d4d4;
  }
  * { box-sizing: border-box; margin: 0; padding: 0; }
  html, body {
    width: 1200px; height: 900px; overflow: hidden;
    background: var(--bg);
  }
  .stage {
    position: relative; width: 1200px; height: 900px;
    display: flex; flex-direction: column; align-items: center; justify-content: center;
    gap: 50px;
  }
  .card {
    position: relative; width: 600px; height: 343px;
    background: var(--card);
    box-shadow: 0 10px 28px rgba(0,0,0,.55);
    overflow: hidden;
  }
  .band {
    position: absolute; left: 0; right: 0; bottom: 0; height: 64px;
    background: var(--orange);
    display: flex; align-items: center; justify-content: center;
    font-family: "Libre Baskerville", Georgia, serif;
    font-weight: 700; text-transform: uppercase;
    color: var(--brown); letter-spacing: .5px;
  }
  /* back */
  .card-back .faint-name {
    position: absolute; left: 0; right: 0; top: 92px;
    text-align: center;
    font-family: "Libre Baskerville", Georgia, serif;
    font-weight: 700; font-size: 46px; letter-spacing: 1px;
    color: var(--faint); text-transform: uppercase;
  }
  .card-back .band { font-size: 17px; }
  /* front */
  .brand {
    position: absolute; left: 36px; top: 78px; width: 230px; height: 170px;
    display: flex; flex-direction: column; align-items: center; justify-content: center; gap: 10px;
  }
  .brand-dot {
    width: 18px; height: 18px; border-radius: 50%; background: var(--orange);
  }
  .brand-name {
    font-family: "Libre Baskerville", Georgia, serif;
    font-weight: 700; font-size: 26px; line-height: 1.2;
    color: var(--orange); text-align: center; text-transform: uppercase;
  }
  .divider {
    position: absolute; left: 292px; top: 24px; width: 1px; height: 230px;
    background: var(--rule);
  }
  .contact {
    position: absolute; left: 318px; top: 40px; right: 16px;
    font-family: "Lato", Arial, sans-serif; color: var(--ink);
  }
  .contact-name {
    font-family: "Libre Baskerville", Georgia, serif;
    font-weight: 700; font-size: 21px; color: var(--brown);
    text-transform: uppercase; margin-bottom: 12px;
  }
  .contact-line {
    display: flex; align-items: center; gap: 8px;
    font-size: 14.5px; line-height: 1.65; white-space: nowrap;
  }
  .contact-line svg { width: 13px; height: 13px; flex: none; fill: var(--ink); }
  .address { font-size: 14.5px; line-height: 1.35; margin-top: 10px; }
  .card-front .band { font-size: 19px; height: 70px; }
</style>
</head>
<body>
<main class="stage">

  <section class="card card-back" aria-label="Card back">
    <div class="faint-name">Prairie Nickel</div>
    <div class="band">We buy &amp; loan on anything of value!</div>
  </section>

  <section class="card card-front" aria-label="Card front">
    <div class="brand">
      <span class="brand-dot"></span>
      <div class="brand-name">Prairie Nickel<br>Pawn</div>
    </div>
    <div class="divider"></div>
    <div class="contact">
      <div class="contact-name">Darren Kellum</div>
      <div class="contact-line">
        <svg viewBox="0 0 24 24"><path d="M6.6 10.8a15 15 0 0 0 6.6 6.6l2.2-2.2a1 1 0 0 1 1-.25 11.4 11.4 0 0 0 3.6.57 1 1 0 0 1 1 1V20a1 1 0 0 1-1 1A17 17 0 0 1 3 4a1 1 0 0 1 1-1h3.5a1 1 0 0 1 1 1c0 1.25.2 2.45.57 3.570a1 1 0 0 1-.25 1z"/></svg>
        972-613-8840
      </div>
      <div class="contact-line">
        <svg viewBox="0 0 24 24"><path d="M2 5h20v14H2z M2 5l10 8 10-8" fill="none" stroke="#2b2b2b" stroke-width="2"/></svg>
        PrairieNickelPawn@Mailvera.com
      </div>
      <div class="contact-line">
        <svg viewBox="0 0 24 24"><circle cx="12" cy="12" r="10"/><path d="M2 12h20M12 2c3 3 3 17 0 20M12 2c-3 3-3 17 0 20" fill="none" stroke="#fff" stroke-width="1.5"/></svg>
        PrairieNickelPawn.com
      </div>
      <div class="address">2417 Hwy 53 S. Suite C Cedar Hollow<br>TX 75246</div>
    </div>
    <div class="band">Offering 10 Month Layaway!</div>
  </section>

</main>
</body>
</html>
```